Redesign Of Current Landing Page

I need to redesign this landing page https://www.brightlanepromo.biz/?page=landing&landing=23 (Please do not opt in because when you do it will show you the home page. Please clear your cookies before going to this url above to view the 1 page landing page.)

Please use my updated website as a reference for colors and logo.
http://sitecradlewerk.com/dh/bpq/index.html

I would like the call to action to be a button that opens into a lead form...

Button would be "Download Samples"

Target Market(s)

small business owners

Industry/Entity Type

Marketing

Number of Pages Required

1 page

Colors

Designer to choose colors to be used in the design.

Requirements
Must have
• must be full responsive on all devices
Nice to have
• must have a legitimate professional apeal to it
Should not have
• open

```html
<!DOCTYPE html>
<html lang="en">
<head>
<meta charset="utf-8">
<title>BrightLane Promo Group – Attract More Customers</title>
<link href="https://fonts.googleapis.com/css2?family=Raleway:wght@400;500;700&family=Open+Sans:ital,wght@0,400;0,600;1,400&display=swap" rel="stylesheet">
<style>
:root{
  --blue:#0a6fc2;
  --blue-deep:#0b63b3;
  --orange:#f9a40e;
  --grey-icon:#9a9a9a;
  --text:#222;
  --muted:#8a8a8a;
  --band:#ececec;
  --footer:#222222;
  --white:#fff;
}
*{margin:0;padding:0;box-sizing:border-box}
html,body{width:1200px;height:2397px;overflow:hidden;background:var(--white)}
body{position:relative;font-family:"Open Sans",Arial,sans-serif;color:var(--text)}
.abs{position:absolute}
.center{text-align:center}

/* header */
.site-header{left:0;top:0;width:1200px;height:112px;background:var(--white);box-shadow:0 3px 8px rgba(0,0,0,.15);z-index:3}
.brand{left:88px;top:30px;display:flex;align-items:center;gap:14px}
.brand-dot{width:54px;height:54px;border-radius:50%;background:var(--blue)}
.brand-name{font-family:"Open Sans",Arial,sans-serif;font-weight:700;font-size:36px;color:#1c1c1c;letter-spacing:.5px}
.contact{top:36px;display:flex;align-items:center;gap:12px;font-size:12px;line-height:17px}
.contact small{display:block;font-size:11px;color:#444}
.contact b{font-weight:600;font-size:13px;color:#111}

/* hero */
.hero{left:0;top:112px;width:1200px;height:560px;overflow:hidden}
.hero-bg{left:0;top:0;width:1200px;height:560px;background:radial-gradient(ellipse at 55% 40%,#ece8e2 0%,#dcd6cd 60%,#cfc8be 100%)}
.hero-title{left:88px;top:134px;font-family:"Raleway",sans-serif;font-weight:700;font-size:60px;line-height:64px;color:var(--blue)}
.hero-sub{left:88px;top:266px;font-size:26px;line-height:37px;color:#444}
.btn{display:block;background:var(--orange);color:var(--white);text-align:center;border-radius:2px}
.hero-btn{left:88px;top:351px;width:233px;height:54px;line-height:54px;font-size:18px;letter-spacing:.3px}
.flyers{left:551px;top:72px;width:552px;height:479px;background:linear-gradient(135deg,#2a5d9c 0%,#7a8fa8 35%,#1f3d25 60%,#7a2a2a 100%);border-radius:4px;box-shadow:6px 10px 18px rgba(0,0,0,.35)}

/* why */
.section-title{left:0;width:1200px;font-family:"Raleway",sans-serif;color:var(--blue);text-align:center}
.rule{height:3px;background:#111}
.why-title{top:768px;font-size:40px}
.why-rule{left:545px;top:830px;width:110px}
.why-sub{left:0;top:850px;width:1200px;font-size:15px;font-family:"Raleway",sans-serif;color:#222}
.feature{width:340px;text-align:center;font-family:"Raleway",sans-serif}
.feature-ring{margin:0 auto;width:160px;height:160px;border-radius:50%;border:4px solid var(--grey-icon);padding:6px}
.feature-ring .disc{width:100%;height:100%;border-radius:50%;background:var(--grey-icon);display:flex;align-items:center;justify-content:center}
.feature.active .feature-ring{border-color:var(--blue)}
.feature.active .disc{background:var(--blue)}
.feature-name{margin-top:22px;font-size:22px;color:#8d8d8d;letter-spacing:.3px}
.feature.active .feature-name{color:var(--blue)}
.feature-desc{margin-top:12px;font-size:13px;line-height:20px;color:#777}
.view-btn{left:522px;top:1234px;width:154px;height:60px;line-height:60px;font-size:19px;font-family:"Raleway",sans-serif}

/* how */
.how{left:0;top:1389px;width:1200px;height:391px;background:var(--band)}
.how-title{top:1446px;font-size:40px;letter-spacing:1px}
.how-rule{left:545px;top:1503px;width:110px}
.how-text{left:192px;top:1536px;width:816px;font-family:"Raleway",sans-serif;font-size:12.5px;line-height:21.5px;color:#a3a3a3;text-align:center}
.read-btn{left:548px;top:1675px;width:107px;height:42px;line-height:42px;font-size:14px;font-family:"Raleway",sans-serif}

/* testimonials */
.clients{left:0;top:1780px;width:1200px;height:417px;background:linear-gradient(90deg,#0b66b5 0%,#1478cc 50%,#0c69b8 100%)}
.clients-title{top:1828px;font-size:38px;color:var(--white)}
.clients-rule{left:545px;top:1895px;width:110px;background:var(--white)}
.card{top:1948px;height:171px;border:1.5px solid rgba(255,255,255,.75)}
.quote{left:-12px;top:-20px;width:38px;height:38px;border-radius:50%;background:var(--white);display:flex;align-items:center;justify-content:center}
.card p{position:absolute;left:12px;top:30px;right:10px;font-style:italic;font-size:12.5px;line-height:22px;color:var(--white)}
.avatar{left:38px;top:114px;width:64px;height:64px;border-radius:50%;border:3px solid #e6e6e6;background:linear-gradient(160deg,#c9a487,#6b4c3b)}
.who{left:130px;top:121px;font-family:"Raleway",sans-serif;font-size:14px;color:var(--white)}
.stars{left:130px;top:142px;display:flex;gap:4px}
.nav{top:2020px;width:29px;height:29px;border-radius:50%;background:#243b52;display:flex;align-items:center;justify-content:center}

/* footer */
.site-footer{left:0;top:2197px;width:1200px;height:200px;background:var(--footer)}
.social{top:2237px;left:526px;display:flex;gap:6px}
.social span{width:32px;height:32px;border-radius:50%}
.footer-rule{left:88px;top:2311px;width:1026px;height:1px;background:#444}
.copyright{left:0;top:2342px;width:1200px;text-align:center;font-size:13.5px;color:#cfcfcf}
</style>
</head>
<body>

<header class="abs site-header">
  <div class="abs brand"><span class="brand-dot"></span><span class="brand-name">BrightLane</span></div>
  <div class="abs contact" style="left:754px">
    <svg width="28" height="28" viewBox="0 0 24 24"><path fill="#0a6fc2" d="M6.6 10.8a15 15 0 0 0 6.6 6.6l2.2-2.2c.3-.3.7-.4 1-.2 1.1.4 2.3.6 3.6.6.6 0 1 .4 1 1V20c0 .6-.4 1-1 1A17 17 0 0 1 3 4c0-.6.4-1 1-1h3.5c.6 0 1 .4 1 1 0 1.3.2 2.5.6 3.6.1.3 0 .7-.2 1z"/></svg>
    <div><small>TOLL FREE</small><b>555-013-4821</b></div>
  </div>
  <div class="abs contact" style="left:938px">
    <svg width="34" height="26" viewBox="0 0 34 26"><rect x="0" y="0" width="34" height="26" rx="3" fill="#0a6fc2"/><path d="M2 3l15 11L32 3" fill="none" stroke="#fff" stroke-width="2.5"/></svg>
    <div><small>QUESTIONS?</small><b>CONTACT THE TEAM</b></div>
  </div>
</header>

<section class="abs hero">
  <div class="abs hero-bg"></div>
  <h1 class="abs hero-title">ATTRACT MORE<br>CUSTOMERS</h1>
  <p class="abs hero-sub">who spend more money with<br>your business more often!</p>
  <a class="abs btn hero-btn">DOWNLOAD SAMPLES</a>
  <svg class="abs" style="left:0;top:450px" width="1200" height="110" viewBox="0 0 1200 110" preserveAspectRratio="none">
    <path d="M0 38 C300 110 700 110 1200 36 L1200 110 L0 110 Z" fill="#fff"/>
    <path d="M0 38 C300 110 700 110 1200 36" fill="none" stroke="#0a6fc2" stroke-width="7"/>
  </svg>
  <div class="abs flyers" role="img" aria-label="Fanned stack of printed incentive certificates: cash back, hotel stay, cruise, media player and city getaway offers"></div>
</section>

<h2 class="abs section-title why-title">Why Offer Incentives To Customers?</h2>
<div class="abs rule why-rule"></div>
<p class="abs center why-sub">Did you know over 90% of texts are read within 3 minutes?</p>

<div class="abs feature" style="left:70px;top:906px">
  <div class="feature-ring"><div class="disc">
    <svg width="70" height="64" viewBox="0 0 70 64" fill="#fff"><rect x="18" y="14" width="6" height="18"/><rect x="28" y="8" width="6" height="24"/><rect x="38" y="2" width="6" height="30"/><path d="M4 42h18l14 6h20l8-6v6l-12 12H20L4 52z"/></svg>
  </div></div>
  <h3 class="feature-name">INCREASE RESPONSES</h3>
  <p class="feature-desc">Increase Responses From<br>Your Existing Ads</p>
</div>
<div class="abs feature active" style="left:420px;top:906px">
  <div class="feature-ring"><div class="disc">
    <svg width="84" height="80" viewBox="0 0 24 23"><path fill="#f9a40e" d="M12 0l3.1 7.2 7.9.7-6 5.2 1.8 7.7L12 16.9 5.2 20.8 7 13.1 1 7.9l7.9-.7z"/></svg>
  </div></div>
  <h3 class="feature-name">BUILD BRAND</h3>
  <p class="feature-desc">Build Brand Awareness<br>and Trust</p>
</div>
<div class="abs feature" style="left:771px;top:906px">
  <div class="feature-ring"><div class="disc">
    <svg width="64" height="64" viewBox="0 0 64 64" fill="#fff"><path d="M58 6c-14 0-26 8-34 22l12 12c14-8 22-20 22-34z"/><circle cx="42" cy="22" r="5" fill="#9a9a9a"/><path d="M22 30l-12 2-6 8 12 2zM34 42l-2 12-8 6-2-12zM18 40l6 6-14 12z"/></svg>
  </div></div>
  <h3 class="feature-name">BOOST</h3>
  <p class="feature-desc">Boost Repeat and Referral<br>Business</p>
</div>

<a class="abs btn view-btn">View More</a>

<section class="abs how"></section>
<h2 class="abs section-title how-title">HOW CAN WE DO IT?</h2>
<div class="abs rule how-rule"></div>
<p class="abs how-text">We help fill empty rooms for thousands of hotels and resorts in hundreds of destinations around the world as well as the major cruise lines. Hotels and resorts are rarely full so when we place someone in their empty rooms, they end up making it up when travelers spend money on room service, spa services, eat at their in-house restaurants, casino and take advantage of other amenities that drive revenue. We also help over 18,000 restaurants, electronic manufacturers, the major gas companies and top grocery chains in the U.S and Canada increase brand awareness as well as increase customer loyalty.</p>
<a class="abs btn read-btn">Read More</a>

<section class="abs clients" role="img" aria-label="Blue-toned photo backdrop of a person working at a desk"></section>
<h2 class="abs section-title clients-title">Our Clients Says</h2>
<div class="abs rule clients-rule"></div>

<div class="abs nav" style="left:27px"><svg width="10" height="14" viewBox="0 0 10 14"><path d="M8 1L2 7l6 6" fill="none" stroke="#fff" stroke-width="2"/></svg></div>
<div class="abs nav" style="left:1144px"><svg width="10" height="14" viewBox="0 0 10 14"><path d="M2 1l6 6-6 6" fill="none" stroke="#fff" stroke-width="2"/></svg></div>

<article class="abs card" style="left:93px;width:330px">
  <span class="abs quote"><svg width="18" height="14" viewBox="0 0 18 14" fill="#0a6fc2"><path d="M0 14V8C0 3 3 0 7 0v3C5 3 4 5 4 7h3v7zM11 14V8c0-5 3-8 7-8v3c-2 0-3 2-3 4h3v7z"/></svg></span>
  <p>Lorem Ipsum is simply dummy text of the printing and typesetting industry. Lorem Ipsum has been the industry's standard dummy..</p>
  <span class="abs avatar" role="img" aria-label="Client portrait"></span>
  <span class="abs who">Marla J Whitcombe</span>
  <span class="abs stars"><svg width="92" height="14" viewBox="0 0 92 14" fill="#f9a40e"><g id="st"><path d="M7 0l1.8 4.4 4.7.4-3.6 3.1 1.1 4.6L7 10 3 12.5l1.1-4.6L.5 4.8l4.7-.4z"/></g><use href="#st" x="19"/><use href="#st" x="38"/><use href="#st" x="57"/><use href="#st" x="76"/></svg></span>
</article>
<article class="abs card" style="left:436px;width:333px">
  <span class="abs quote"><svg width="18" height="14" viewBox="0 0 18 14" fill="#0a6fc2"><path d="M0 14V8C0 3 3 0 7 0v3C5 3 4 5 4 7h3v7zM11 14V8c0-5 3-8 7-8v3c-2 0-3 2-3 4h3v7z"/></svg></span>
  <p>Lorem Ipsum is simply dummy text of the printing and typesetting industry. Lorem Ipsum has been the industry's standard dummy..</p>
  <span class="abs avatar" role="img" aria-label="Client portrait"></span>
  <span class="abs who">Renata K Ashford</span>
  <span class="abs stars"><svg width="92" height="14" viewBox="0 0 92 14" fill="#f9a40e"><use href="#st"/><use href="#st" x="19"/><use href="#st" x="38"/><use href="#st" x="57"/><use href="#st" x="76"/></svg></span>
</article>
<article class="abs card" style="left:781px;width:333px">
  <span class="abs quote"><svg width="18" height="14" viewBox="0 0 18 14" fill="#0a6fc2"><path d="M0 14V8C0 3 3 0 7 0v3C5 3 4 5 4 7h3v7zM11 14V8c0-5 3-8 7-8v3c-2 0-3 2-3 4h3v7z"/></svg></span>
  <p>Lorem Ipsum is simply dummy text of the printing and typesetting industry. Lorem Ipsum has been the industry's standard dummy..</p>
  <span class="abs avatar" role="img" aria-label="Client portrait"></span>
  <span class="abs who">Celia M Dunmore</span>
  <span class="abs stars"><svg width="92" height="14" viewBox="0 0 92 14" fill="#f9a40e"><use href="#st"/><use href="#st" x="19"/><use href="#st" x="38"/><use href="#st" x="57"/><use href="#st" x="76"/></svg></span>
</article>

<footer class="abs site-footer"></footer>
<div class="abs social">
  <span style="background:#3b5a9a"></span><span style="background:#2a9fd8"></span><span style="background:#d8392b"></span><span style="background:#c4302b"></span>
</div>
<div class="abs footer-rule"></div>
<p class="abs copyright">Copyright © 2017. BrightLane Promo Group, Inc. All rights reserved.</p>

</body>
</html>
```